Brivane Management

We need a web design for a new consulting company, with clients all over the world. The company provides management consulting to the travel industry.

Logo files are attached.

Website must look very corporate and be responsive in design.

Management Consulting

```html
<!DOCTYPE html>
<html lang="en">
<head>
<meta charset="utf-8">
<title>Brivane Management</title>
<link rel="stylesheet" href="https://fonts.googleapis.com/css2?family=Bree+Serif&family=Oxygen:wght@400;700&family=Roboto+Slab:wght@400&display=swap">
<style>
:root{
  --blue:#0f6fc0;
  --navy:#0d2a4a;
  --ink:#333;
  --muted:#555;
  --icon:#1e1e1e;
  --band:#ececec;
  --rule:#d6d6d6;
  --footer-top:#3a3a3a;
  --footer-bottom:#1c1c1c;
  --panel:#2e2e2e;
  --white:#fff;
}
*{box-sizing:border-box;margin:0;padding:0}
html,body{width:882px;height:1200px;overflow:hidden}
body{position:relative;font-family:"Oxygen",sans-serif;color:var(--ink);background:var(--white);font-size:10px}
.abs{position:absolute}

/* brand */
.brand{display:flex;align-items:center;gap:9px}
.brand-mark{width:30px;height:30px;background:var(--navy)}
.brand-name{font-family:"Roboto Slab",serif;color:var(--navy);font-size:22px;line-height:1;letter-spacing:.5px}
.brand-name small{display:block;font-size:8px;letter-spacing:1.2px;margin-top:3px}

/* header */
.site-header{left:0;top:0;width:882px;height:78px;background:linear-gradient(#fafafa,#eaeaea);border-top:3px solid #9a9a9a;border-bottom:1px solid #d0d0d0}
.site-header .brand{position:absolute;left:106px;top:21px}
.phone{left:673px;top:14px;font-size:15px;color:#222;display:flex;align-items:center;gap:6px}
.main-nav{left:524px;top:44px;display:flex;font-size:11px}
.main-nav a{color:#333;text-decoration:none;padding:0 11px;border-left:1px solid #bbb;line-height:13px}
.main-nav a:first-child{border:0;color:var(--blue);text-decoration:underline}

/* hero */
.hero{left:0;top:78px;width:882px;height:327px;background:linear-gradient(180deg,#cfe6f7 0%,#eaf3fa 35%,#7fb2cf 62%,#2f86b0 78%,#c9a27a 100%)}
.hero-caption{left:0;top:372px;width:882px;height:33px;background:rgba(20,30,40,.72);color:var(--white);font-size:18.5px;text-align:center;line-height:33px;letter-spacing:.2px}
.slide-arrow{width:30px;height:30px;border-radius:50%;background:#1b1b1b;border:2px solid #555;display:flex;align-items:center;justify-content:center}

/* about */
.about-title{left:0;top:418px;width:882px;display:flex;justify-content:center;align-items:center;gap:12px}
.section-title{font-family:"Bree Serif",serif;font-size:19px;color:var(--navy);letter-spacing:.5px;font-weight:400}
.section-title em{font-style:normal;color:var(--blue)}
.about-title .brand{gap:6px}
.about-title .brand-mark{width:20px;height:20px}
.about-title .brand-name{font-size:16px}
.about-title .brand-name small{font-size:5.5px;margin-top:1px}
.about-text{left:108px;top:456px;width:666px;text-align:center;font-size:10px;line-height:15.3px;color:var(--muted)}

/* services */
.services{left:0;top:535px;width:882px;height:198px;background:var(--band);border-top:1px solid var(--rule);border-bottom:1px solid var(--rule)}
.services .section-title{position:absolute;top:17px;width:100%;text-align:center}
.service{position:absolute;top:63px;width:150px;text-align:center}
.service-icon{display:block;margin:0 auto}
.service-label{font-family:"Roboto Slab",serif;font-size:11px;line-height:11.5px;color:#222;margin-top:18px;letter-spacing:.3px}

/* columns */
.col-title{font-family:"Bree Serif",serif;font-weight:400;font-size:16px;color:var(--navy);display:flex;align-items:center;gap:6px;border-bottom:1px solid var(--rule);padding-bottom:4px;width:100%}
.col-title em{font-style:normal;color:var(--blue)}
.news{left:104px;top:759px;width:207px}
.news-item{padding:9px 0 7px;border-bottom:1px dashed #ccc;font-size:9.5px;line-height:13px;color:#333}
.news-item:last-of-type{border:0}
.news-item b{display:block;font-size:10px}
.read-more{display:block;text-align:right;color:var(--blue);font-weight:700;font-size:9px;margin-top:4px}
.testimonial{left:337px;top:759px;width:208px}
.quote{margin-top:12px;background:#eaeaea;border-radius:8px;padding:9px 8px 30px 20px;font-style:italic;font-size:9.5px;line-height:13px;color:#444}
.client-row{display:flex;align-items:flex-end;gap:12px;margin:-10px 0 0 14px;font-size:9.5px}
.client-row span{padding-bottom:10px}
.client-photo{width:48px;height:48px;border:3px solid var(--white);box-shadow:0 0 2px #999;background:linear-gradient(#c9d3dd,#6d7d8d)}
.contact{left:571px;top:759px;width:208px}
.field{display:block;width:208px;height:21px;border:1px solid #c8c8c8;border-radius:3px;margin-top:5px;font-size:9px;color:#888;font-style:italic;padding:4px 6px;background:#fff}
.field:first-of-type{margin-top:12px}
.field.message{height:53px}
.submit{margin-top:9px;background:linear-gradient(#2b6bb0,#0d3f7a);color:var(--white);font-weight:700;font-size:11px;width:50px;height:17px;border-radius:2px;text-align:center;line-height:17px}

/* clients */
.clients{left:0;top:953px;width:882px;height:132px;background:var(--band);border-top:1px solid var(--rule)}
.clients .section-title{position:absolute;top:16px;width:100%;text-align:center}
.client-logo{position:absolute;top:55px;height:55px;background:var(--white);display:flex;align-items:center;justify-content:center;gap:6px;font-family:"Oxygen",sans-serif;font-weight:700;font-size:14px;color:#333;white-space:nowrap}
.dot{width:11px;height:11px;border-radius:50%;background:#333}

/* footer */
.site-footer{left:0;top:1085px;width:882px;height:115px;background:linear-gradient(var(--footer-top),var(--footer-bottom));color:#ddd}
.foot-box{position:absolute;top:19px;height:57px;background:var(--panel);border:1px solid #4a4a4a;padding:4px 8px;font-size:8px}
.foot-box h4{font-weight:700;font-size:10.5px;color:#eee;margin-bottom:8px}
.news-input{display:flex;gap:6px}
.news-input span{width:130px;height:20px;background:#555;border-radius:2px;font-style:italic;color:#ccc;font-size:8.5px;padding:4px 6px}
.news-input i{width:22px;height:20px;background:#777;border-radius:2px;display:flex;align-items:center;justify-content:center}
.social{display:flex;gap:8px}
.social span{width:19px;height:19px;background:#2d78c0}
.site-footer .brand{position:absolute;left:570px;top:29px}
.site-footer .brand-mark{width:34px;height:34px;background:var(--white)}
.site-footer .brand-name{color:var(--white);font-size:23px}
.foot-links{left:105px;top:90px;font-size:8.5px;color:#ddd}
.copyright{left:631px;top:90px;font-size:8.5px;color:#ddd}
</style>
</head>
<body>

<header class="site-header abs">
  <div class="brand">
    <div class="brand-mark"></div>
    <div class="brand-name">BRIVANE<small>STRATEGY MANAGEMENT, INC.</small></div>
  </div>
  <div class="phone abs">
    <svg width="14" height="14" viewBox="0 0 14 14"><rect width="14" height="14" rx="2" fill="#0f6fc0"/><path d="M4 3.5c0 4 2.5 6.5 6.5 7l1-1.6-2-1.2-.9.9C7.4 8 6 6.6 5.4 5.4l.9-.9-1.2-2z" fill="#fff"/></svg>
    123 456 7890
  </div>
  <nav class="main-nav abs"><a href="#">Home</a><a href="#">About Us</a><a href="#">Services</a><a href="#">Contact Us</a></nav>
</header>

<section class="hero abs" role="img" aria-label="Collage of world landmarks, a crashing wave, an airliner and a smiling travelling family"></section>
<div class="slide-arrow abs" style="left:73px;top:216px"><svg width="8" height="12"><path d="M6 1 1 6l5 5" stroke="#fff" stroke-width="1.6" fill="none"/></svg></div>
<div class="slide-arrow abs" style="left:781px;top:216px"><svg width="8" height="12"><path d="M2 1l5 5-5 5" stroke="#fff" stroke-width="1.6" fill="none"/></svg></div>
<div class="hero-caption abs">WE PROVIDE A CUSTOMIZED PLAN FOR FINANCIAL IMPROVEMENT</div>

<div class="about-title abs">
  <h2 class="section-title"><em>ABOUT</em></h2>
  <div class="brand"><div class="brand-mark"></div><div class="brand-name">BRIVANE<small>STRATEGY MANAGEMENT, INC.</small></div></div>
</div>
<p class="about-text abs">Lorem ipsum dolor sit amet, consectetuer adipiscing elit,Sed diam nonummy nibh euismod tincidunt ut laoreet dolore magna aliquam erat volutpat. Ut wisi enim ad minim veniam, quis nostrud exerci tation ullamcorper suscipit lobortis nisl ut aliquip &nbsp;commodo consequat. Duis autem vel eum iriure dolor in hendrerit in vulputate velit esse molestie consequat, vel ill dolore eu feugiat nulla facilisis at vero eros et accumsan et iusto odio dignissim qui blandit praesent luptatumdeelenit augue duis dolore te feugait nulla facilisi.</p>

<svg width="0" height="0" style="position:absolute">
  <defs>
    <radialGradient id="disc" cx="50%" cy="50%" r="50%">
      <stop offset="0" stop-color="#ffffff"/><stop offset=".7" stop-color="#f2f2f2"/><stop offset="1" stop-color="#cfcfcf"/>
    </radialGradient>
    <g id="disc-base">
      <circle cx="38" cy="38" r="37" fill="url(#disc)"/>
      <path d="M10 44A29 29 0 0 1 58 16" stroke="#cfe5c0" stroke-width="7" fill="none"/>
      <path d="M66 32A29 29 0 0 1 24 64" stroke="#c6c6c6" stroke-width="7" fill="none"/>
    </g>
  </defs>
</svg>

<section class="services abs">
  <h2 class="section-title"><em>OUR</em> SERVICES</h2>
  <div class="service" style="left:93px">
    <svg class="service-icon" width="76" height="76" viewBox="0 0 76 76" role="img" aria-label="Rising bar chart icon"><use href="#disc-base"/>
      <g fill="var(--icon)"><rect x="18" y="46" width="6" height="12"/><rect x="27" y="40" width="6" height="18"/><rect x="36" y="34" width="6" height="24"/><rect x="45" y="28" width="6" height="30"/><rect x="15" y="58" width="40" height="2"/></g>
      <path d="M18 40 44 20" stroke="var(--icon)" stroke-width="3"/><path d="M40 16h9v9z" fill="var(--icon)"/></svg>
    <div class="service-label">SALES/<br>MARKETING</div>
  </div>
  <div class="service" style="left:223px">
    <svg class="service-icon" width="76" height="76" viewBox="0 0 76 76" role="img" aria-label="Clock and planner icon"><use href="#disc-base"/>
      <rect x="17" y="20" width="26" height="32" rx="2" fill="var(--icon)"/><rect x="21" y="27" width="18" height="2" fill="#fff"/><rect x="21" y="33" width="14" height="2" fill="#fff"/>
      <circle cx="46" cy="48" r="12" fill="#fff" stroke="var(--icon)" stroke-width="3"/><path d="M46 41v7h5" stroke="var(--icon)" stroke-width="2" fill="none"/></svg>
    <div class="service-label">STRATEGIC<br>PLANNING</div>
  </div>
  <div class="service" style="left:360px">
    <svg class="service-icon" width="76" height="76" viewBox="0 0 76 76" role="img" aria-label="Coin and bag icon"><use href="#disc-base"/>
      <rect x="16" y="24" width="22" height="28" rx="3" fill="var(--icon)"/>
      <circle cx="45" cy="46" r="13" fill="var(--icon)"/><circle cx="45" cy="46" r="9.5" fill="none" stroke="#fff" stroke-width="1.5"/>
      <path d="M48 41.5c-1-1-5-1.5-5 1s5 1.5 5 4-4 2-5.5 1M45.3 39v14" stroke="#fff" stroke-width="1.6" fill="none"/></svg>
    <div class="service-label" style="margin-top:13px">HUMAN CAPITAL<br>MANAGEMENT SOLUTIONS</div>
  </div>
  <div class="service" style="left:511px">
    <svg class="service-icon" width="76" height="76" viewBox="0 0 76 76" role="img" aria-label="Chart under magnifier icon"><use href="#disc-base"/>
      <rect x="16" y="22" width="34" height="26" fill="#fff" stroke="var(--icon)" stroke-width="3"/>
      <path d="M20 42l7-9 6 5 8-9 6 5" stroke="var(--icon)" stroke-width="2.2" fill="none"/>
      <circle cx="50" cy="49" r="6.5" fill="#fff" stroke="var(--icon)" stroke-width="3"/><path d="M54.5 53.5 61 60" stroke="var(--icon)" stroke-width="4"/></svg>
    <div class="service-label">FINANCIAL<br>ANALYSIS</div>
  </div>
  <div class="service" style="left:646px">
    <svg class="service-icon" width="76" height="76" viewBox="0 0 76 76" role="img" aria-label="Briefcase with coin icon"><use href="#disc-base"/>
      <path d="M31 27v-4h14v4" stroke="var(--icon)" stroke-width="3" fill="none"/>
      <rect x="17" y="27" width="40" height="24" rx="3" fill="var(--icon)"/><rect x="17" y="36" width="40" height="2" fill="#fff"/><rect x="34" y="34" width="6" height="6" fill="#fff"/>
      <circle cx="55" cy="50" r="8" fill="#fff" stroke="var(--icon)" stroke-width="2"/><path d="M57 47c-1-1-4-1-4 .8s4 1.2 4 3-3 1.6-4 .8M55.2 45v10" stroke="var(--icon)" stroke-width="1.3" fill="none"/></svg>
    <div class="service-label">CASH MANAGEMENT<br>SOLUTIONS</div>
  </div>
</section>

<section class="news abs">
  <h3 class="col-title"><svg width="18" height="14" viewBox="0 0 18 14"><path d="M1 5h4l8-4v12L5 9H1z" fill="#333"/><rect x="4" y="9" width="3" height="4" fill="#333"/></svg><span><em>LATEST</em> NEWS</span></h3>
  <div class="news-item"><b>09/10/2014</b>Lorem ipsum dolor sit amet, cctetuer adipiscingin elit, sed diam nummy nibh eui smod tinciduntiot vulputate velit esse molestie</div>
  <div class="news-item"><b>10/10/2014</b>Lorem ipsum dolor sit amet, cctetuer adipiscingin elit, sed diam nummy nibh eui smod tinciduntiot vulputate velit esse molestie</div>
  <a class="read-more">Read more »</a>
</section>

<section class="testimonial abs">
  <h3 class="col-title"><svg width="16" height="14" viewBox="0 0 16 14"><path d="M1 1h10v6H5l-3 3V7H1z" fill="#333"/><path d="M12 4h3v6h-1v3l-3-3H6V8h6z" fill="#333"/></svg><span><em>CLIENT</em> TESTIMONIAL</span></h3>
  <div class="quote">Duis autem vel eum iriureol hder in vultat velit esse moles conqat vela ilu dolor feugiat.Duis autem vel eum ure hendrern vultat velit esse autm vel eum iriure dol</div>
  <div class="client-row"><div class="client-photo" role="img" aria-label="Portrait of the client"></div><span>Mr. Dolore Eu Feugiat</span></div>
  <a class="read-more" style="margin-top:-2px">Read more »</a>
</section>

<section class="contact abs">
  <h3 class="col-title"><svg width="16" height="14" viewBox="0 0 16 14"><rect x="1" y="3" width="9" height="10" fill="none" stroke="#333" stroke-width="1.5"/><path d="M6 9l8-8 1.5 1.5-8 8H6z" fill="#333"/></svg><span><em>QUICK</em> CONTACT</span></h3>
  <div class="field">Name</div>
  <div class="field">Email</div>
  <div class="field message">Message</div>
  <div class="submit">Submit</div>
</section>

<section class="clients abs">
  <h2 class="section-title">OUR <em>CLIENTS</em></h2>
  <div class="slide-arrow abs" style="left:82px;top:66px;width:22px;height:22px"><svg width="6" height="10"><path d="M5 1 1 5l4 4" stroke="#fff" stroke-width="1.5" fill="none"/></svg></div>
  <div class="client-logo" style="left:117px;width:104px">Meridian Tech</div>
  <div class="client-logo" style="left:231px;width:117px">Archvale</div>
  <div class="client-logo" style="left:356px;width:139px"><span class="dot"></span>Hopwell</div>
  <div class="client-logo" style="left:517px;width:100px">Trevance</div>
  <div class="client-logo" style="left:637px;width:130px">Ledgerly</div>
  <div class="slide-arrow abs" style="left:778px;top:66px;width:22px;height:22px"><svg width="6" height="10"><path d="M1 1l4 4-4 4" stroke="#fff" stroke-width="1.5" fill="none"/></svg></div>
</section>

<footer class="site-footer abs">
  <div class="foot-box" style="left:104px;width:180px">
    <h4>Subscribe to Newsletter</h4>
    <div class="news-input"><span>Email here</span><i><svg width="6" height="9"><path d="M1 1l4 3.5L1 8" stroke="#fff" stroke-width="1.6" fill="none"/></svg></i></div>
  </div>
  <div class="foot-box" style="left:305px;width:118px">
    <h4>Contact Us</h4>
    <div style="display:flex;gap:6px;align-items:center;margin-bottom:4px"><svg width="8" height="8"><path d="M1 1c0 3.5 2.5 6 6 6l1-1.5-2-1-1 .8C4 5 3 4 2.7 3L3.5 2l-1-2z" fill="#ccc"/></svg>123 456 7890</div>
    <div style="display:flex;gap:6px;align-items:center"><svg width="9" height="7"><rect width="9" height="7" fill="#ccc"/><path d="M0 0l4.5 4L9 0" stroke="#333" fill="none"/></svg>info@brivane.com</div>
  </div>
  <div class="foot-box" style="left:444px;width:86px">
    <h4>Follow Us</h4>
    <div class="social"><span aria-label="Social profile one"></span><span aria-label="Social profile two" style="background:#1da1d8"></span><span aria-label="Social profile three" style="background:#1b6ea8"></span></div>
  </div>
  <div class="brand"><div class="brand-mark"></div><div class="brand-name">BRIVANE<small>STRATEGY MANAGEMENT, INC.</small></div></div>
  <div class="foot-links abs">Home &nbsp;| &nbsp;About Us &nbsp;| &nbsp;Services &nbsp;| &nbsp;Contact Us &nbsp;| &nbsp;Terms Conditions</div>
  <div class="copyright abs">© 2014 &nbsp;Brivane. All Rights Reserved</div>
</footer>

</body>
</html>
```